Vehicle accessory sales website

We need a refreshed design for our vehicle accessory. This website is used to select vehicle year, make, model, trim and then displays products available for the vehicle you selected. The design needs to be responsive over mobile, tablet and desktop.

Current site: https://kelvorautoparts.example/vehicle-search/

We are only looking for an updated UI on the vehcile search function, not the website itself.

I want one full screen that is a Year, Make, Model and Trim Selection, this is a stamdalone page with no header, not a website page.

Then a screen that shows the vehicle selected at the top (Not a vehicle image) and the available product categories.

Then a screen that still shows the products avaiable after selecting the category

Then a product pop up

Then a checkout screen

Target Market(s)

Car dealership customers and salespeople

Industry/Entity Type

Automotive accessories

Number of Pages Required

3 page

Requirements
Must have
• Vehicle selection page, main category page, product page after category has been selected, product pop up and checkout screen

```html
<!DOCTYPE html>
<html lang="en">
<head>
<meta charset="utf-8">
<title>Vehicle Accessory Search</title>
<link rel="stylesheet" href="https://fonts.googleapis.com/css2?family=Roboto:wght@400;500&display=swap">
<style>
  :root {
    --page-bg: #e6e7e9;
    --panel-bg: #ffffff;
    --ink: #111111;
    --ink-soft: #555a60;
    --line: #dcdde0;
    --card-line: #e3e4e7;
    --white: #ffffff;
    --button-bg: #0b0b0b;
  }
  * { box-sizing: border-box; margin: 0; padding: 0; }
  html, body {
    width: 828px; height: 1200px; overflow: hidden;
    background: var(--page-bg);
    font-family: "Roboto", Arial, sans-serif;
    color: var(--ink);
  }
  .canvas { position: relative; width: 828px; height: 1200px; }

  /* Vehicle selector */
  .vehicle-select {
    position: absolute; left: 79px; top: 70px; width: 690px; height: 310px;
    background:
      linear-gradient(180deg, rgba(40,38,34,0.55) 0%, rgba(0,0,0,0) 35%, rgba(0,0,0,0.15) 100%),
      linear-gradient(180deg, #5c5850 0%, #8a7f6d 28%, #6f6a5e 42%, #4a4a3c 58%, #3e3a2c 75%, #6b5a40 100%);
  }
  .vehicle-select__title {
    position: absolute; top: 36px; left: 6px; width: 100%;
    text-align: center; color: var(--white);
    font-size: 24px; line-height: 34px; font-weight: 500; letter-spacing: 0.2px;
  }
  .vehicle-select__rule {
    position: absolute; top: 84px; left: 327px; width: 31px; height: 3px; background: var(--white);
  }
  .field {
    position: absolute; width: 184px; height: 28px;
    background: var(--white); border-radius: 7px;
    display: flex; align-items: center; padding: 0 12px;
    font-size: 8px; color: var(--ink);
  }
  .field svg.icon { width: 11px; height: 11px; margin-right: 7px; flex: none; }
  .field .chevron { margin-left: auto; width: 10px; height: 10px; }
  .field--make { left: 148px; top: 127px; }
  .field--year { left: 340px; top: 127px; }
  .field--model { left: 148px; top: 168px; }
  .field--trim { left: 340px; top: 167px; }
  .view-button {
    position: absolute; left: 148px; top: 211px; width: 376px; height: 43px;
    background: var(--button-bg); border: 1px solid rgba(255,255,255,0.35);
    border-radius: 9px; color: var(--white);
    display: flex; align-items: center; justify-content: center;
    font-size: 13.5px;
  }

  /* Category panel */
  .category-panel {
    position: absolute; left: 79px; top: 436px; width: 691px; height: 666px;
    background: var(--panel-bg);
  }
  .breadcrumb {
    height: 26px; border-bottom: 1px solid var(--line);
    display: flex; align-items: center; padding-left: 80px;
    font-size: 6.5px; color: var(--ink-soft); gap: 6px;
  }
  .breadcrumb .sep { margin: 0 2px; }
  .category-title {
    position: absolute; left: 78px; top: 46px;
    font-size: 19px; font-weight: 500;
  }
  .category-rule { position: absolute; left: 78px; top: 81px; width: 24px; height: 2px; background: var(--ink); }
  .search {
    position: absolute; left: 439px; top: 50px; width: 175px; height: 28px;
    border: 1px solid var(--line); border-radius: 4px;
    display: flex; align-items: center; padding-left: 11px;
    font-size: 6.5px; color: var(--ink-soft);
  }
  .search svg { width: 8px; height: 8px; margin-right: 8px; }
  .category-grid {
    position: absolute; left: 77px; top: 113px;
    display: grid; grid-template-columns: repeat(4, 127px);
    column-gap: 10.5px; row-gap: 22px;
  }
  .category-card {
    height: 158px; border: 1px solid var(--card-line); border-radius: 3px;
    background: var(--white); overflow: hidden;
  }
  .category-card__media { height: 111px; }
  .category-card__label {
    text-align: center; font-size: 9px; margin-top: 16px; color: var(--ink);
  }
  .m-blackout { background: linear-gradient(180deg, #ffffff 0%, #e9eaec 50%, #ffffff 100%); }
  .m-blind { background: linear-gradient(135deg, #d4d7dc 0%, #9aa7bd 45%, #8c96a6 70%, #c3c7cd 100%); }
  .m-ceramic { background: linear-gradient(110deg, #b3121a 0%, #cf2a30 45%, #7d7f83 80%, #9a9c9f 100%); }
  .m-dash { background: linear-gradient(170deg, #1c1c1c 0%, #0a0a0a 60%, #151515 100%); }
  .m-mats { background: linear-gradient(180deg, #ffffff 0%, #ebebeb 50%, #ffffff 100%); }
  .m-gps { background: linear-gradient(100deg, #7a5a2a 0%, #3a4f8f 40%, #4a5a88 60%, #a8824e 100%); }
  .m-seat { background: linear-gradient(180deg, #ffffff 0%, #eeeae6 50%, #ffffff 100%); }
  .m-media { background: linear-gradient(180deg, #ffffff 0%, #e8e9ec 50%, #ffffff 100%); }
  .m-ppf { background: linear-gradient(180deg, #ffffff 0%, #e6eeee 55%, #ffffff 100%); }
  .m-parking { background: linear-gradient(160deg, #c3c6ca 0%, #dcdee1 50%, #aeb2b7 100%); }
  .m-radar { background: linear-gradient(180deg, #0d0d0d 0%, #2a1a14 55%, #0b0b0b 100%); }
  .m-tint { background: linear-gradient(130deg, #2a2b2d 0%, #7d7f82 45%, #3a3b3d 100%); }
</style>
</head>
<body>
<div class="canvas">

  <section class="vehicle-select" role="img" aria-label="Winding road through misty mountain hills at dusk">
    <h1 class="vehicle-select__title">Select Your Vehicle</h1>
    <div class="vehicle-select__rule"></div>

    <div class="field field--make">
      <svg class="icon" viewBox="0 0 24 24" fill="none" stroke="#222" stroke-width="1.8"><path d="M4 15v-3l2-5h12l2 5v3z"/><path d="M3 12h18"/><circle cx="7.5" cy="15" r="1.5"/><circle cx="16.5" cy="15" r="1.5"/><path d="M5 15v3M19 15v3"/></svg>
      Select a Make
      <svg class="chevron" viewBox="0 0 24 24" fill="none" stroke="#222" stroke-width="2"><path d="M4 8l8 8 8-8"/></svg>
    </div>
    <div class="field field--year">
      <svg class="icon" viewBox="0 0 24 24" fill="none" stroke="#222" stroke-width="1.8"><rect x="3" y="5" width="18" height="16" rx="1"/><path d="M3 10h18M8 3v4M16 3v4"/></svg>
      Select a Year
      <svg class="chevron" viewBox="0 0 24 24" fill="none" stroke="#222" stroke-width="2"><path d="M4 8l8 8 8-8"/></svg>
    </div>
    <div class="field field--model">
      <svg class="icon" viewBox="0 0 24 24" fill="none" stroke="#222" stroke-width="1.6"><circle cx="12" cy="12" r="3"/><path d="M12 2l2 3 3.5-1 .5 3.5 3.5 1-1.5 3.5 1.5 3.5-3.5 1-.5 3.5-3.5-1-2 3-2-3-3.5 1-.5-3.5-3.5-1L4.5 12 3 8.5l3.5-1L7 4l3.5 1z"/></svg>
      Select a Model
      <svg class="chevron" viewBox="0 0 24 24" fill="none" stroke="#222" stroke-width="2"><path d="M4 8l8 8 8-8"/></svg>
    </div>
    <div class="field field--trim">
      <svg class="icon" viewBox="0 0 24 24" fill="none" stroke="#222" stroke-width="1.8"><path d="M6 2v16h16"/><path d="M2 6h16v16"/></svg>
      Select a Trim
      <svg class="chevron" viewBox="0 0 24 24" fill="none" stroke="#222" stroke-width="2"><path d="M4 8l8 8 8-8"/></svg>
    </div>
    <div class="view-button">View Accessories</div>
  </section>

  <section class="category-panel">
    <nav class="breadcrumb">
      <span>Averon</span><span class="sep">-</span><span>2024</span><span class="sep">-</span><span>V3</span><span class="sep">-</span><span>Premium</span><span class="sep">-</span><span>ACCESSORIES</span>
    </nav>
    <h2 class="category-title">Select Category</h2>
    <div class="category-rule"></div>
    <div class="search">
      <svg viewBox="0 0 24 24" fill="none" stroke="#333" stroke-width="2.4"><circle cx="10" cy="10" r="7"/><path d="M15 15l6 6"/></svg>
      Search by product Name, Part Number or Brand
    </div>

    <div class="category-grid">
      <div class="category-card"><div class="category-card__media m-blackout" role="img" aria-label="Black grille, door handles and mirror caps"></div><p class="category-card__label">Blackout</p></div>
      <div class="category-card"><div class="category-card__media m-blind" role="img" aria-label="Cars on a road with blind spot zones highlighted"></div><p class="category-card__label">Blind Spot Monitoring</p></div>
      <div class="category-card"><div class="category-card__media m-ceramic" role="img" aria-label="Gloved hand applying coating to a red car"></div><p class="category-card__label">Ceramic Coating</p></div>
      <div class="category-card"><div class="category-card__media m-dash" role="img" aria-label="Front and rear dash camera units"></div><p class="category-card__label">Dash Cams</p></div>

      <div class="category-card"><div class="category-card__media m-mats" role="img" aria-label="Black molded floor and cargo mats"></div><p class="category-card__label">Floor/Cargo Mats</p></div>
      <div class="category-card"><div class="category-card__media m-gps" role="img" aria-label="Hand holding a phone showing a navigation map"></div><p class="category-card__label">GPS Tracking</p></div>
      <div class="category-card"><div class="category-card__media m-seat" role="img" aria-label="Car seat with heated zones shown in orange"></div><p class="category-card__label">Heated Seating</p></div>
      <div class="category-card"><div class="category-card__media m-media" role="img" aria-label="Overhead and headrest entertainment screens"></div><p class="category-card__label">Mobile Entertainment</p></div>

      <div class="category-card"><div class="category-card__media m-ppf" role="img" aria-label="SUV with protective film shown in teal"></div><p class="category-card__label">Paint Protection Film</p></div>
      <div class="category-card"><div class="category-card__media m-parking" role="img" aria-label="Top view of a car with parking sensor waves"></div><p class="category-card__label">Parking Assist and Cameras</p></div>
      <div class="category-card"><div class="category-card__media m-radar" role="img" aria-label="Dashboard gauges with radar alert display and remote"></div><p class="category-card__label">Radar and Laser Protection</p></div>
      <div class="category-card"><div class="category-card__media m-tint" role="img" aria-label="Hands applying tint film to a car window"></div><p class="category-card__label">Window Tint</p></div>
    </div>
  </section>

</div>
</body>
</html>
```